Moravel Aesthetic Doctor

I require an elegant, luxurious looking business card for my aesthetic business. I am a doctor and that will set me aside from competitors. I am planning to provide home and spa based treatments to clients with high expectations. I have attached my logo.

```html
<!DOCTYPE html>
<html lang="en">
<head>
<meta charset="utf-8">
<title>Moravel Aesthetic Doctor – Business Card</title>
<link href="https://fonts.googleapis.com/css2?family=Montserrat:wght@400;500&family=Roboto:ital,wght@0,400;1,400&display=swap" rel="stylesheet">
<style>
  :root {
    --page: #c9c9c9;
    --blue-light: #4fa9de;
    --blue-deep: #0b5e9f;
    --band-grey: #8f9aab;
    --card-white: #f3f3f3;
    --ink: #3a3d42;
    --accent: #3e9ad6;
    --wave-blue: #4ea3d8;
    --wave-grey: #8c95a5;
    --logo-grey: #7c8594;
    --white: #ffffff;
  }
  * { box-sizing: border-box; margin: 0; padding: 0; }
  html, body { width: 1200px; height: 576px; overflow: hidden; background: var(--page); }
  .canvas { position: relative; width: 1200px; height: 576px; }

  .card {
    position: absolute; top: 138px; width: 484px; height: 294px;
    border-radius: 11px; overflow: hidden;
  }

  /* Front */
  .card--front {
    left: 82px;
    background: linear-gradient(160deg, var(--blue-light) 0%, #2a86c6 45%, var(--blue-deep) 100%);
    color: var(--white);
  }
  .front-brand { position: absolute; left: 58px; top: 50px; display: flex; align-items: center; gap: 18px; }
  .brand-mark { width: 96px; height: 96px; border-radius: 50%; border: 3px solid rgba(255,255,255,0.9); }
  .brand-name { font-family: "Montserrat", sans-serif; font-weight: 400; color: var(--white); line-height: 1; }
  .brand-name .word { display: block; font-size: 42px; letter-spacing: 3px; }
  .brand-name .tag { display: block; font-size: 19px; letter-spacing: 2.4px; margin-top: 6px; }
  .services {
    position: absolute; top: 196px; left: 0; width: 100%; text-align: center;
    font-family: "Roboto", sans-serif; font-size: 13px; line-height: 18px; color: var(--white);
  }
  .services .sep { margin: 0 8px; }
  .front-band {
    position: absolute; top: 246px; left: 0; width: 100%; height: 22px;
    background: var(--band-grey); text-align: center;
    font-family: "Montserrat", sans-serif; font-size: 12px; letter-spacing: 0.8px; line-height: 22px;
    color: #eef1f5;
  }

  /* Back */
  .card--back { left: 602px; background: var(--card-white); }
  .wave { position: absolute; left: 0; top: 0; width: 484px; height: 294px; }
  .person { position: absolute; left: 28px; top: 40px; font-family: "Roboto", sans-serif; }
  .person-name { font-size: 19px; color: var(--ink); }
  .person-post { font-size: 10px; font-style: italic; color: var(--accent); margin-top: 3px; }
  .person-cred { font-size: 13px; color: var(--accent); line-height: 16px; margin-top: 8px; }

  .back-brand { position: absolute; left: 218px; top: 42px; display: flex; align-items: center; gap: 10px; }
  .back-brand .brand-mark { width: 64px; height: 64px; border: 2px solid var(--logo-grey); }
  .back-brand .brand-name { color: var(--logo-grey); }
  .back-brand .brand-name .word { font-size: 30px; letter-spacing: 1.5px; }
  .back-brand .brand-name .tag { font-size: 13.5px; letter-spacing: 1.2px; margin-top: 4px; }

  .contact { position: absolute; left: 28px; top: 160px; font-family: "Roboto", sans-serif; font-size: 13px; color: var(--ink); }
  .contact-row { display: flex; align-items: center; height: 20px; }
  .contact-item { display: flex; align-items: center; gap: 7px; margin-right: 14px; }
  .icon { width: 11px; height: 11px; fill: var(--accent); }
  .social-dot { display: inline-block; width: 13px; height: 13px; border-radius: 50%; background: var(--accent); margin-left: 4px; }

  .back-tagline {
    position: absolute; right: 24px; top: 230px; text-align: right;
    font-family: "Montserrat", sans-serif; font-size: 13px; line-height: 18px; color: #eaf4fb;
  }
</style>
</head>
<body>
<main class="canvas">

  <section class="card card--front" aria-label="Card front">
    <div class="front-brand">
      <span class="brand-mark"></span>
      <div class="brand-name"><span class="word">MORAVEL</span><span class="tag">AESTHETIC DOCTOR</span></div>
    </div>
    <p class="services">
      Dermal Injectables<span class="sep">|</span>Plasma Facials<span class="sep">|</span>Microneedling<br>
      Skin Boosters<span class="sep">|</span>Excessive Sweating
    </p>
    <div class="front-band">HOME AND SPA BASED TREATMENTS</div>
  </section>

  <section class="card card--back" aria-label="Card back">
    <svg class="wave" viewBox="0 0 484 294" preserveAspectRatio="none" aria-hidden="true">
      <path d="M0 240 C90 300 200 300 300 250 C380 210 430 200 484 200 L484 294 L0 294 Z" fill="var(--wave-blue)"/>
      <path d="M0 226 C100 262 200 250 300 218 C390 190 440 180 484 182 L484 190 C440 188 390 198 300 228 C200 262 100 274 0 240 Z" fill="var(--wave-grey)"/>
      <path d="M40 268 C140 282 240 262 320 232 C250 268 150 290 40 268 Z" fill="var(--wave-grey)" opacity="0.8"/>
    </svg>

    <div class="person">
      <p class="person-name">Dr Elise Varent</p>
      <p class="person-post">MRCPCH MD</p>
      <p class="person-cred">Australasian Diploma of<br>Aesthetic Medicine</p>
    </div>

    <div class="back-brand">
      <span class="brand-mark"></span>
      <div class="brand-name"><span class="word">MORAVEL</span><span class="tag">AESTHETIC DOCTOR</span></div>
    </div>

    <div class="contact">
      <div class="contact-row">
        <span class="contact-item">
          <svg class="icon" viewBox="0 0 12 12" aria-hidden="true"><path d="M0 2h12v8H0z M0 2l6 4 6-4" /></svg>
          elise@moravel.co.nz
        </span>
        <span class="contact-item">
          <svg class="icon" viewBox="0 0 12 12" aria-hidden="true"><circle cx="6" cy="6" r="6"/></svg>
          www.moravel.co.nz
        </span>
      </div>
      <div class="contact-row">
        <span class="contact-item">
          <svg class="icon" viewBox="0 0 12 12" aria-hidden="true"><path d="M2 0h3l1 3-2 1.5a7 7 0 0 0 3.5 3.5L9 6l3 1v3c0 1-1 2-2 2C4.5 12 0 7.5 0 2c0-1 1-2 2-2z"/></svg>
          0800 555 014
        </span>
      </div>
      <div class="contact-row">
        Follow us on:&nbsp;<span class="social-dot"></span><span class="social-dot"></span>
      </div>
    </div>

    <p class="back-tagline">Home and Spa<br>Based Treatments</p>
  </section>

</main>
</body>
</html>
```